Online Shop - Website Design for up an coming art studio

We require a fully functional website design - not just design - but complete coded online shop website please, which should be a word press style frame work to allow ease up updating the site in the future. The website will sell art work from up and coming artists. The business is called "Brindle Harbor Studios". I have attached our logo to allow the submitted designs to tie in with this.

Industry/Entity Type

Shop

Coding

Coded - Design and coding required

Number of Pages Required

1 page

Colors

Designer to choose colors to be used in the design.

Requirements
Must have
• The website design must incorporate and fully functional online eCommerce shop feature.

```html
<!DOCTYPE html>
<html lang="en">
<head>
<meta charset="utf-8">
<title>Brindle Harbor Studios</title>
<link href="https://fonts.googleapis.com/css2?family=Fredoka:wght@500;600&family=Open+Sans:wght@400;600;700&display=swap" rel="stylesheet">
<style>
:root{
  --red:#d3092f;
  --ink:#222;
  --text:#555;
  --muted:#888;
  --orange:#f7941d;
  --yellow:#f8cf1b;
  --purple:#7b2fa0;
  --white:#fff;
  --rainbow:linear-gradient(90deg,#f79a1b 0%,#ef5a3a 22%,#d81b60 40%,#8e2a9c 58%,#e2442e 78%,#f8cf1b 100%);
  --head:"Fredoka",sans-serif;
  --body:"Open Sans",sans-serif;
}
*{box-sizing:border-box;margin:0;padding:0}
html,body{width:1200px;height:5114px;overflow:hidden}
body{position:relative;font-family:var(--body);color:var(--text);background:var(--white)}
.section{position:absolute;left:0;width:1200px}
.btn{display:inline-flex;align-items:center;justify-content:center;height:40px;padding:0 26px;border-radius:20px;font:700 12px var(--body);text-transform:uppercase;letter-spacing:.5px;background:var(--red);color:var(--white)}
.btn-outline{background:var(--white);color:var(--red);border:2px solid var(--red)}
.section-title{font:600 44px var(--head);text-transform:uppercase;letter-spacing:1px}
.rainbow-text{background:var(--rainbow);-webkit-background-clip:text;background-clip:text;color:transparent}
.round-arrow{width:30px;height:30px;border-radius:50%;background:#eee;display:flex;align-items:center;justify-content:center}

/* Header */
.site-header{top:0;height:153px;background:var(--white)}
.brand{position:absolute;left:100px;top:28px;display:flex;align-items:center;gap:12px}
.brand-dot{width:56px;height:56px;border-radius:50%;background:var(--red)}
.brand-name{font:700 22px var(--body);color:var(--ink);width:170px;line-height:1.1}
.main-nav{position:absolute;right:100px;top:68px;display:flex;gap:32px;align-items:center;font:600 13px var(--body);text-transform:uppercase;color:var(--ink)}
.main-nav .active{color:var(--red);border-bottom:2px solid var(--red);padding-bottom:6px}
.cart{width:44px;height:44px;border-radius:50%;background:var(--red);display:flex;align-items:center;justify-content:center}

/* Hero */
.hero{top:153px;height:600px;overflow:hidden;border-radius:0 0 50% 50%/0 0 16% 16%}
.hero-photo{position:absolute;inset:0;background:linear-gradient(100deg,#1d4b8a 0%,#3a8ccf 28%,#b8d3e6 52%,#e7d6c6 66%,#d9273d 82%,#f2efe9 100%)}
.hero-title{position:absolute;left:100px;top:190px;font:600 58px var(--head);color:var(--white);letter-spacing:1px;text-transform:uppercase}
.hero-sub{position:absolute;left:100px;top:275px;font:400 20px var(--body);color:var(--white)}
.hero .btn{position:absolute;left:100px;top:345px}
.hero-dots{position:absolute;right:42px;top:240px;display:flex;flex-direction:column;gap:10px}
.hero-dots span{width:10px;height:10px;border-radius:50%;background:rgba(255,255,255,.6)}
.hero-dots span:first-child{background:var(--red)}

/* About */
.about{top:790px;height:400px;text-align:center}
.about .section-title{margin-top:35px}
.about p{width:960px;margin:22px auto 0;font-size:13px;line-height:26px}
.about-actions{margin-top:28px;display:flex;gap:16px;justify-content:center}
.about-art{position:absolute;right:0;top:240px;width:190px;height:160px;background:linear-gradient(120deg,#2ca0e0,#8e2a9c,#e2442e,#f8cf1b);border-radius:60% 0 0 60%}

/* Services */
.services{top:1217px;height:556px;background:var(--rainbow)}
.services .section-title{position:absolute;left:100px;top:60px;color:var(--white)}
.view-all{position:absolute;right:100px;top:62px;height:40px;padding:0 22px;border-radius:20px;background:rgba(255,255,255,.35);color:var(--white);font:600 12px var(--body);display:flex;align-items:center;text-transform:uppercase}
.service-card{position:absolute;top:163px;width:318px;height:325px;background:var(--white);padding:40px 22px 0;box-shadow:0 6px 16px rgba(0,0,0,.15)}
.service-card h3{font:700 15px var(--body);color:var(--red);text-transform:uppercase;margin:16px 0 12px}
.service-card p{font-size:12px;line-height:22px;color:var(--muted)}
.service-card .go{position:absolute;left:50%;bottom:-15px;margin-left:-20px;width:40px;height:40px;border-radius:50%;background:var(--red);display:flex;align-items:center;justify-content:center}
.service-card.is-highlight{background:var(--red)}
.service-card.is-highlight h3{color:var(--yellow)}
.service-card.is-highlight p{color:var(--white)}
.service-card.is-highlight .go{background:var(--white)}

/* New releases */
.releases{top:1773px;height:560px;background:linear-gradient(135deg,#f1f1f1 0%,#fafafa 40%,#ececec 70%,#f7f7f7 100%)}
.releases .section-title{position:absolute;left:100px;top:80px}
.releases .intro{position:absolute;left:100px;top:150px;width:360px;font-size:12px;line-height:22px}
.releases .read-more{position:absolute;left:100px;top:300px}
.carousel{position:absolute;left:512px;top:110px;width:586px;height:250px}
.slide{position:absolute;top:20px;width:160px;height:220px;background:var(--white);padding:8px;box-shadow:0 4px 10px rgba(0,0,0,.2)}
.slide div{width:100%;height:100%}
.slide-main{position:absolute;left:163px;top:-10px;width:260px;height:290px;background:#111;padding:10px;box-shadow:0 6px 16px rgba(0,0,0,.3)}
.slide-main .art{height:200px;background:linear-gradient(160deg,#8a7d6a,#c9b89a,#6f6a60)}
.slide-main .caption{background:var(--white);height:60px;padding:8px 12px;position:relative}
.slide-main .caption strong{font:700 13px var(--body);color:var(--ink)}
.slide-main .caption small{display:block;font-size:9px;color:var(--muted);width:150px;line-height:12px}
.slide-price{position:absolute;right:12px;top:18px;font:700 18px var(--body);color:var(--ink)}
.car-arrow{position:absolute;top:110px;width:30px;height:44px;background:#333;display:flex;align-items:center;justify-content:center}
.releases .gallery{position:absolute;left:740px;top:430px}

/* Products */
.products{top:2353px;height:870px}
.products .section-title{position:absolute;left:100px;top:50px}
.pager{position:absolute;right:100px;top:58px;display:flex;gap:8px}
.product{position:absolute;width:1000px;left:100px;height:300px}
.product-img{position:absolute;width:400px;height:295px}
.product-info{position:absolute;width:500px}
.product-info h3{font:600 20px var(--body);color:var(--ink);text-transform:uppercase;line-height:32px}
.product-info p{font-size:12px;line-height:22px;margin-top:14px}
.price{margin-top:20px;font:700 26px var(--body);color:var(--red)}
.price s{color:#bbb;font-weight:400;margin-left:12px}
.product-info .btn{margin-top:14px}

/* Testimonials */
.testimonials{top:3240px;height:460px;background:var(--rainbow)}
.testimonials .section-title{position:absolute;left:100px;top:60px;color:var(--white)}
.portrait{position:absolute;left:150px;top:190px;width:160px;height:160px;transform:rotate(45deg);border:10px solid var(--red);background:linear-gradient(135deg,#8b6b5a,#d9b9a2)}
.quote{position:absolute;left:392px;top:185px;width:700px;color:var(--white);font-size:13px;line-height:24px}
.quote cite{display:block;margin-top:10px;font:700 14px var(--body);color:var(--yellow);font-style:normal}
.test-arrows{position:absolute;right:110px;top:340px;display:flex;gap:14px}

/* Featured collections */
.collections{top:3750px;height:660px}
.collections .section-title{position:absolute;left:100px;top:20px}
.collections .pager{top:22px}
.collection-main{position:absolute;left:100px;top:115px;width:487px;height:368px;background:linear-gradient(160deg,#f6b13a 0%,#e1573b 45%,#5a2d5e 80%,#2b2340 100%)}
.collection-label{position:absolute;right:20px;bottom:40px;width:170px;background:rgba(255,255,255,.9);padding:14px;font:700 14px var(--body);color:var(--ink);text-transform:uppercase;line-height:20px}
.collection-label .btn{height:26px;padding:0 12px;font-size:10px;margin-top:8px}
.thumb{position:absolute;top:495px;width:112px;height:130px}
.collection-custom{position:absolute;left:604px;top:115px;width:240px;height:510px;background:var(--orange);padding:20px 16px}
.collection-offer{position:absolute;left:860px;top:115px;width:240px;height:510px;background:#b9a384;padding:20px 16px;text-align:center}
.collection-custom h3,.collection-offer h3{font:600 34px var(--head);color:var(--white);text-transform:uppercase;line-height:36px}
.collection-custom small{display:block;font:700 10px var(--body);color:var(--white);margin:8px 0;text-transform:uppercase}
.tag{display:inline-block;background:var(--red);color:var(--white);font:700 10px var(--body);padding:6px 10px;text-transform:uppercase}

/* Map */
.map{top:4467px;height:280px;border-top:4px solid transparent;border-image:var(--rainbow) 1 0 0 0}
.map-area{position:absolute;inset:0;background:linear-gradient(120deg,#e8e6e1,#f1efea 50%,#e3e1dc)}
.address{position:absolute;left:460px;top:80px;width:290px;height:118px;background:var(--white);box-shadow:0 4px 12px rgba(0,0,0,.15);text-align:center;padding:20px 16px;font-size:12px;line-height:20px;color:var(--purple)}

/* Footer */
.site-footer{top:4752px;height:362px;border-top:4px solid transparent;border-image:var(--rainbow) 1 0 0 0;text-align:center}
.social{position:absolute;left:0;right:0;top:145px;display:flex;justify-content:center;gap:14px}
.social span{width:44px;height:44px;border-radius:50%}
.footer-rule{position:absolute;left:540px;top:220px;width:120px;height:2px;background:var(--rainbow)}
.copyright{position:absolute;left:0;right:0;top:282px;font-size:11px;color:var(--muted)}
</style>
</head>
<body>

<header class="section site-header">
  <div class="brand"><span class="brand-dot"></span><span class="brand-name">Brindle Harbor Studios</span></div>
  <nav class="main-nav">
    <span class="active">Home</span><span>About us</span><span>Services</span><span>Projects</span><span>Blog</span><span>Contact us</span>
    <span class="cart"><svg width="18" height="18" viewBox="0 0 24 24" fill="#fff"><path d="M3 4h3l2 11h11l2-8H7"/><circle cx="9" cy="19" r="1.7"/><circle cx="17" cy="19" r="1.7"/></svg></span>
  </nav>
</header>

<section class="section hero">
  <div class="hero-photo" role="img" aria-label="Smiling painter in a red apron holding brushes in front of a colourful abstract canvas"></div>
  <h1 class="hero-title">Brindle Harbor Studios</h1>
  <p class="hero-sub">We sell artwork from upcoming artists</p>
  <span class="btn">Shop now</span>
  <div class="hero-dots"><span></span><span></span><span></span><span></span><span></span></div>
</section>

<section class="section about">
  <h2 class="section-title rainbow-text">About Brindle Harbor Studios</h2>
  <p>Sed ut perspiciatis unde omnis iste natus error sit voluptatem accusantium doloremque laudantium, totam rem aperiam, eaque ipsa quae ab illo inventore veritatis et quasi architecto beatae vitae dicta sunt explicabo. Nemo enim ipsam voluptatem quia voluptas sit aspernatur aut odit aut fugit, sed quia consequuntur magni dolores eos qui ratione voluptatem sequi nesciunt. Neque porro quisquam est, qui dolorem ipsum quia dolor sit amet, consectetur, adipisci velit, sed quia non numquam eius modi tempora incidunt ut labore et dolore magnam aliquam quaerat voluptatem. Ut enim ad minima veniam, quis nostrum exercitationem.</p>
  <div class="about-actions"><span class="btn">Read more</span><span class="btn btn-outline">Shop now</span></div>
  <div class="about-art" role="img" aria-label="Flowing rainbow coloured hair strands illustration"></div>
</section>

<section class="section services">
  <h2 class="section-title">Our Services</h2>
  <span class="view-all">View all</span>
  <article class="service-card is-highlight" style="left:100px">
    <svg width="34" height="34" viewBox="0 0 24 24" fill="#f8cf1b"><path d="M21 6.5a5 5 0 0 1-6.6 4.7L6 19.6a2 2 0 0 1-2.8-2.8l8.4-8.4A5 5 0 0 1 17.5 2l-3 3 .6 2.9 2.9.6z"/></svg>
    <h3>Interior Design</h3>
    <p>Nemo enim ipsam voluptatem quia voluptas sit aspernatur aut odit aut fugit, sed quia consequuntur magni dolores eos qui ratione ut odit aut fugit voluptatem.</p>
    <span class="go"><svg width="14" height="14" viewBox="0 0 24 24" fill="none" stroke="#d3092f" stroke-width="3"><path d="M6 6l6 6-6 6M13 6l6 6-6 6"/></svg></span>
  </article>
  <article class="service-card" style="left:441px">
    <svg width="34" height="34" viewBox="0 0 24 24" fill="#f8cf1b"><rect x="3" y="3" width="8" height="8"/><rect x="13" y="3" width="8" height="8"/><rect x="3" y="13" width="8" height="8"/><rect x="13" y="13" width="8" height="8"/></svg>
    <h3>Floor Design</h3>
    <p>Nemo enim ipsam voluptatem quia voluptas sit aspernatur aut odit aut fugit, sed quia consequuntur magni dolores eos qui ratione ut odit aut fugit voluptatem.</p>
    <span class="go"><svg width="14" height="14" viewBox="0 0 24 24" fill="none" stroke="#fff" stroke-width="3"><path d="M6 6l6 6-6 6M13 6l6 6-6 6"/></svg></span>
  </article>
  <article class="service-card" style="left:782px">
    <svg width="34" height="34" viewBox="0 0 24 24" fill="#f8cf1b"><path d="M12 3l10 9h-3v9h-5v-6h-4v6H5v-9H2z"/></svg>
    <h3>Exterior Design</h3>
    <p>Nemo enim ipsam voluptatem quia voluptas sit aspernatur aut odit aut fugit, sed quia consequuntur magni dolores eos qui ratione ut odit aut fugit voluptatem.</p>
    <span class="go"><svg width="14" height="14" viewBox="0 0 24 24" fill="none" stroke="#fff" stroke-width="3"><path d="M6 6l6 6-6 6M13 6l6 6-6 6"/></svg></span>
  </article>
</section>

<section class="section releases">
  <h2 class="section-title rainbow-text">New Releases</h2>
  <p class="intro">Nam libero tempore, cum soluta nobis est eligendi optio cumque nihil impedit quo minus id quod maxime placeat facere possimus, omnis voluptas assumenda est, omnis dolor repellendus. Temporibus autem quibusdam et aut officiis debitis aut rerum necessitatibus saepe eveniet ut et voluptates repudiandae.</p>
  <span class="btn btn-outline read-more">Read more</span>
  <div class="carousel">
    <div class="slide" style="left:0"><div role="img" aria-label="Framed landscape painting" style="background:linear-gradient(160deg,#9aa0a3,#d7d2c8,#7c7f77)"></div></div>
    <div class="slide" style="left:426px"><div role="img" aria-label="Framed colourful street art" style="background:linear-gradient(160deg,#4f7fa8,#c7a46a,#3e4f5d)"></div></div>
    <div class="slide-main">
      <div class="art" role="img" aria-label="Featured new artwork in a dark frame"></div>
      <div class="caption"><strong>Lorem ipsum</strong><small>Dui ipsum ut libero sed in ipsum sed dolor in</small><span class="slide-price">$50</span></div>
    </div>
    <span class="car-arrow" style="left:0"><svg width="12" height="12" viewBox="0 0 24 24" fill="#fff"><path d="M16 4L6 12l10 8z"/></svg></span>
    <span class="car-arrow" style="right:0"><svg width="12" height="12" viewBox="0 0 24 24" fill="#fff"><path d="M8 4l10 8-10 8z"/></svg></span>
  </div>
  <span class="btn gallery">View our gallery</span>
</section>

<section class="section products">
  <h2 class="section-title rainbow-text">Our Products</h2>
  <div class="pager">
    <span class="round-arrow"><svg width="10" height="10" viewBox="0 0 24 24" fill="none" stroke="#555" stroke-width="3"><path d="M15 4l-8 8 8 8"/></svg></span>
    <span class="round-arrow"><svg width="10" height="10" viewBox="0 0 24 24" fill="none" stroke="#555" stroke-width="3"><path d="M9 4l8 8-8 8"/></svg></span>
  </div>
  <article class="product" style="top:157px">
    <div class="product-img" style="left:0;background:linear-gradient(135deg,#7a1f6d,#b1287f,#5b1656)" role="img" aria-label="Paint brushes in bright colours on a purple background"></div>
    <div class="product-info" style="left:443px;top:0">
      <h3>Non numquam eius modi tempora incidunt ut labore</h3>
      <p>Sed ut perspiciatis unde omnis iste natus error sit voluptatem accusantium doloremque laudantium, totam rem aperiam, eaque ipsa quae ab illo inventore veritatis et quasi architecto beatae vitae dicta sunt explicabo.</p>
      <div class="price">$76.18<s>$86.18</s></div>
      <span class="btn">Shop now</span>
    </div>
  </article>
  <article class="product" style="top:505px">
    <div class="product-info" style="left:0;top:0">
      <h3>Den numquam eius modi tempora incidunt ut lagee</h3>
      <p>Sed ut perspiciatis unde omnis iste natus error sit voluptatem accusantium doloremque laudantium, totam rem aperiam, eaque ipsa quae ab illo inventore veritatis et quasi architecto beatae vitae dicta sunt explicabo.</p>
      <div class="price">$26.18<s>$86.18</s></div>
      <span class="btn">Shop now</span>
    </div>
    <div class="product-img" style="left:572px;background:linear-gradient(135deg,#e9e6e3,#d8cfc9,#e56fa0)" role="img" aria-label="Hands working with colour swatches on a designer's desk"></div>
  </article>
</section>

<section class="section testimonials">
  <h2 class="section-title">Testimonials</h2>
  <div class="portrait" role="img" aria-label="Portrait of the client"></div>
  <blockquote class="quote">“Neque porro quisquam est, qui dolorem ipsum quia dolor sit amet, consectetur, adipisci velit, sed quia non numquam eius modi tempora incidunt ut labore et dolore magnam aliquam quaerat voluptatem. Ut enim ad minima veniam, quis nostrum exercitationem ullam corporis suscipit laboriosam, nisi ut aliquid ex ea commodi consequatur.”<cite>- Ravel Architects</cite></blockquote>
  <div class="test-arrows">
    <svg width="12" height="14" viewBox="0 0 24 24" fill="none" stroke="#fff" stroke-width="3"><path d="M15 4l-8 8 8 8"/></svg>
    <svg width="12" height="14" viewBox="0 0 24 24" fill="none" stroke="#fff" stroke-width="3"><path d="M9 4l8 8-8 8"/></svg>
  </div>
</section>

<section class="section collections">
  <h2 class="section-title rainbow-text">Featured Collections</h2>
  <div class="pager">
    <span class="round-arrow"><svg width="10" height="10" viewBox="0 0 24 24" fill="none" stroke="#555" stroke-width="3"><path d="M15 4l-8 8 8 8"/></svg></span>
    <span class="round-arrow"><svg width="10" height="10" viewBox="0 0 24 24" fill="none" stroke="#555" stroke-width="3"><path d="M9 4l8 8-8 8"/></svg></span>
  </div>
  <div class="collection-main" role="img" aria-label="Painting of a red tree on a hill at sunset">
    <div class="collection-label">Lorem ipsum is simply dummy text of<br><span class="btn">Buy now</span></div>
  </div>
  <div class="thumb" style="left:100px;background:linear-gradient(135deg,#b2452f,#e0a07a)" role="img" aria-label="Wall of framed prints"></div>
  <div class="thumb" style="left:225px;background:linear-gradient(135deg,#444,#bbb)" role="img" aria-label="Black and white sketch"></div>
  <div class="thumb" style="left:350px;background:linear-gradient(135deg,#e43f5a,#3aa36a)" role="img" aria-label="Tropical flower print"></div>
  <div class="thumb" style="left:475px;background:linear-gradient(135deg,#c24c8b,#2d8bc9)" role="img" aria-label="Colourful pop art print"></div>
  <div class="collection-custom">
    <h3>Custom Artwork</h3>
    <small>Lorem ipsum is simply</small>
    <span class="tag">View all collections</span>
    <div style="margin-top:40px;height:310px;background:linear-gradient(160deg,#f2f2f2,#c54a7a,#333)" role="img" aria-label="Collage of custom framed artworks"></div>
  </div>
  <div class="collection-offer">
    <h3>10%<br>Offer</h3>
    <span class="tag" style="margin-top:12px">Special offers</span>
    <div style="margin-top:30px;height:330px;background:#111;padding:14px"><div style="height:100%;background:linear-gradient(160deg,#6f8a8f,#d8d0b8,#4b5f4f)" role="img" aria-label="Framed nature quote print"></div></div>
  </div>
</section>

<section class="section map">
  <div class="map-area" role="img" aria-label="Street map of the studio location"></div>
  <div class="address">
    <svg width="20" height="26" viewBox="0 0 24 30" fill="#d3092f"><path d="M12 0a10 10 0 0 0-10 10c0 8 10 20 10 20s10-12 10-20A10 10 0 0 0 12 0zm0 14a4 4 0 1 1 0-8 4 4 0 0 1 0 8z"/></svg><br>
    42 Larkmoor Lane, Eastvale,<br>Northshire, AB1 2CD
  </div>
</section>

<footer class="section site-footer">
  <div class="social">
    <span style="background:#f7941d" role="img" aria-label="Social link"></span>
    <span style="background:#1da1f2" role="img" aria-label="Social link"></span>
    <span style="background:#f7941d" role="img" aria-label="Social link"></span>
    <span style="background:#e0442e" role="img" aria-label="Social link"></span>
  </div>
  <div class="footer-rule"></div>
  <p class="copyright">© copyright 2017 Brindle Harbor Studios. All Rights Reserved.</p>
</footer>

</body>
</html>
```